Tech business card design

We need an amazing business card design for our new business 'Pexla' a marketing tech startup based in Sydney, Australia. We provide an online marketplace for businesses to search and buy advertising media, connect with service providers and learn more about marketing. We wish to communicate 'cool tech', reliability and professionalism and design based around our logo.

Target Market(s)

Business Owners

Contact Information for Business Card

Name
Position
Email Address
Website
Phone Number

Font styles to use
Other font styles liked:
• Avenir & Avenir Next

Colors

Designer to choose colors to be used in the design.

```html
<!DOCTYPE html>
<html lang="en">
<head>
<meta charset="utf-8">
<title>Pexla Business Card</title>
<link rel="stylesheet" href="https://fonts.googleapis.com/css2?family=Mulish:wght@300;400;600;800&display=swap">
<style>
  :root {
    --backdrop: #3a332f;
    --card: #1c1d1f;
    --card-edge: #26272a;
    --ink: #ffffff;
    --ink-soft: #d9d9d9;
    --emboss: #b9bcbf;
    --divider: #cfcfcf;
  }
  * { margin: 0; padding: 0; box-sizing: border-box; }
  html, body {
    width: 1200px;
    height: 864px;
    overflow: hidden;
    background: var(--backdrop);
    font-family: "Mulish", "Avenir Next", Avenir, sans-serif;
  }
  .stage {
    position: relative;
    width: 1200px;
    height: 864px;
  }
  .card {
    position: absolute;
    width: 620px;
    height: 379px;
    background: var(--card);
    border: 1px solid var(--card-edge);
    border-radius: 3px;
    box-shadow: 0 10px 28px rgba(0,0,0,0.45);
  }
  .card--front { left: 80px; top: 34px; }
  .card--back { left: 500px; top: 451px; }

  /* Front */
  .front-wordmark {
    position: absolute;
    left: 0; right: 0;
    top: 96px;
    text-align: center;
    font-weight: 800;
    font-size: 128px;
    line-height: 1;
    letter-spacing: -3px;
    color: var(--emboss);
  }
  .front-web {
    position: absolute;
    left: 0; right: 0;
    top: 262px;
    text-align: center;
    font-weight: 400;
    font-size: 15px;
    letter-spacing: 7px;
    color: var(--ink-soft);
  }

  /* Back */
  .back-wordmark {
    position: absolute;
    left: 44px;
    top: 140px;
    font-weight: 800;
    font-size: 82px;
    line-height: 1;
    letter-spacing: -2px;
    color: var(--ink);
  }
  .back-divider {
    position: absolute;
    left: 322px;
    top: 108px;
    width: 1px;
    height: 170px;
    background: var(--divider);
  }
  .contact {
    position: absolute;
    left: 348px;
    top: 122px;
    color: var(--ink);
  }
  .contact-name {
    font-weight: 600;
    font-size: 22px;
    letter-spacing: 0.5px;
    line-height: 1.1;
  }
  .contact-role {
    font-weight: 300;
    font-size: 18px;
    letter-spacing: 0.5px;
    margin-bottom: 14px;
  }
  .contact-list { list-style: none; }
  .contact-item {
    display: flex;
    align-items: center;
    gap: 10px;
    font-weight: 300;
    font-size: 15px;
    line-height: 24px;
  }
  .contact-icon {
    width: 13px;
    height: 13px;
    flex: none;
    fill: none;
    stroke: var(--ink);
    stroke-width: 1.6;
  }
</style>
</head>
<body>
<main class="stage">
  <section class="card card--front" aria-label="Card front">
    <div class="front-wordmark">pexla</div>
    <div class="front-web">www.pexlamedia.com.au</div>
  </section>

  <section class="card card--back" aria-label="Card back">
    <div class="back-wordmark">pexla</div>
    <div class="back-divider"></div>
    <div class="contact">
      <div class="contact-name">MARCUS REID</div>
      <div class="contact-role">FOUNDER, DIRECTOR</div>
      <ul class="contact-list">
        <li class="contact-item">
          <svg class="contact-icon" viewBox="0 0 14 14" aria-hidden="true"><rect x="3.5" y="1" width="7" height="12" rx="1.2"/><line x1="6" y1="11" x2="8" y2="11"/></svg>
          +61 (0)400 555 018
        </li>
        <li class="contact-item">
          <svg class="contact-icon" viewBox="0 0 14 14" aria-hidden="true"><rect x="1" y="3" width="12" height="8.5" rx="1"/><polyline points="1,3.5 7,8 13,3.5"/></svg>
          marcus@pexlamedia.com.au
        </li>
        <li class="contact-item">
          <svg class="contact-icon" viewBox="0 0 14 14" aria-hidden="true"><circle cx="7" cy="7" r="5.8"/><line x1="1.2" y1="7" x2="12.8" y2="7"/><ellipse cx="7" cy="7" rx="2.6" ry="5.8"/></svg>
          www.pexlamedia.com.au
        </li>
      </ul>
    </div>
  </section>
</main>
</body>
</html>
```